Delegate visit agenda

We need a creative, yet simple and official design for an agenda to be handed out for delegates visiting our organization. The design needs to be creative, informative and visual when possible. Flat design is desired but other options are welcomed. The agenda should be 3 pages in lengths only. Page 1 should have the company logo with an event title (with the ability to add country flag) and the dates of the event. Pages 2 should include photos of receiving delegate (e.g. VIPs) and any other relevant people. Page 3 should include agenda entries with the following information: title of entry, date and time, location, relevant pictures (e.g. a hotel or flight). The generic style of an infographic.
Updates
Project Deadline Extended
Reason: Not enough submissions received.
No optimal design (i.e. creative and attractive) received.

Brief has been updated with samples.

Target Market(s)
Very high profile people (e.g. presidents, ministers, GM,...etc.)
Industry/Entity Type
Hotel
Colors
Designer to choose colors to be used in the design.
Look and feel
Each slider illustrates characteristics of the customer's brand and the style your logo design should communicate.

```html
<!DOCTYPE html>
<html lang="en">
<head>
<meta charset="utf-8">
<title>Growing Future Relations — Delegate Agenda</title>
<link rel="stylesheet" href="https://fonts.googleapis.com/css2?family=Libre+Baskerville:wght@700&display=swap">
<style>
  :root {
    --gold: #c0882d;
    --ink: #1d1d1b;
    --crest-red: #e63a44;
    --paper: #ffffff;
  }
  * { margin: 0; padding: 0; box-sizing: border-box; }
  html, body {
    width: 1200px;
    height: 849px;
    overflow: hidden;
    background: var(--paper);
  }
  .cover {
    position: relative;
    width: 1200px;
    height: 849px;
    background: var(--paper);
    font-family: "Libre Baskerville", "Baskerville", Georgia, serif;
    font-weight: 700;
    color: var(--gold);
  }
  .event-title {
    position: absolute;
    right: 92px;
    top: 52px;
    text-align: right;
    font-size: 86px;
    line-height: 101px;
    letter-spacing: 1px;
    text-transform: uppercase;
  }
  .event-title span { display: block; }
  .event-dates {
    position: absolute;
    right: 92px;
    top: 420px;
    font-size: 32px;
    letter-spacing: 0.5px;
    text-transform: uppercase;
  }
  .host {
    position: absolute;
    left: 110px;
    top: 430px;
    width: 360px;
    text-align: center;
  }
  .host-mark {
    display: block;
    margin: 0 auto 34px;
  }
  .host-name {
    font-size: 19px;
    color: var(--ink);
    text-transform: uppercase;
    letter-spacing: 0.3px;
  }
  .intro {
    position: absolute;
    left: 100px;
    right: 100px;
    top: 766px;
    text-align: center;
    font-size: 12.5px;
    line-height: 18px;
  }
</style>
</head>
<body>
  <main class="cover">
    <h1 class="event-title">
      <span>Growing</span>
      <span>Future</span>
      <span>Relations</span>
    </h1>

    <p class="event-dates">10-12 February 2015</p>

    <div class="host">
      <svg class="host-mark" width="170" height="170" viewBox="0 0 170 170" aria-hidden="true">
        <circle cx="85" cy="85" r="85" fill="var(--crest-red)"/>
      </svg>
      <p class="host-name">Office of Trade Partnerships</p>
    </div>

    <p class="intro">
      Lorem ipsum dolor sit amet, error regione voluptua mea ei, ei ullum civibus efficiantur pri. Ei exerci reprimique has. Duo te dicant complectitur, pri ei nihil munere doctus. Vix id exerci verear, mea ea accusata petentium ullamcorper. Vel offendit percipit maluisset ea.
    </p>
  </main>
</body>
</html>
```